Letterhead, stationery and email signature for construction business

I need the letterhead, stationery and email signature designs for a construction business. I want them to have a corporate feel to them.

I've attached the logo for reference.

```html
<!DOCTYPE html>
<html lang="en">
<head>
<meta charset="utf-8">
<title>Harlow Build – Stationery</title>
<link href="https://fonts.googleapis.com/css2?family=Arimo:wght@400;700&family=Mulish:wght@600;700&display=swap" rel="stylesheet">
<style>
  :root{
    --brand-blue:#2f55a4;
    --brand-slate:#4b4c57;
    --ink:#55565e;
    --ink-soft:#6a6b72;
    --rule:#4b4c57;
    --paper:#ffffff;
    --backdrop:#dcdcdc;
    --sig-tone:#c9cad0;
  }
  *{margin:0;padding:0;box-sizing:border-box}
  html,body{width:918px;height:1200px;overflow:hidden}
  body{background:var(--backdrop);font-family:"Arimo",Arial,sans-serif;color:var(--ink);position:relative}

  .sheet{position:absolute;background:var(--paper);overflow:hidden}
  .letterhead{left:111px;top:67px;width:555px;height:784px}
  .business-card{left:115px;top:886px;width:547px;height:207px}

  .brand{position:absolute;display:flex;align-items:center;gap:6px;color:var(--brand-blue);font-weight:700;white-space:nowrap}
  .brand-square{background:var(--brand-blue);display:block;flex:none}
  .letterhead .brand{left:50px;top:41px;height:44px;font-size:17px}
  .letterhead .brand-square{width:16px;height:16px}
  .business-card .brand{left:46px;top:54px;height:61px;font-size:22px;gap:8px}
  .business-card .brand-square{width:20px;height:20px}

  .v-divider{position:absolute;width:1px;background:var(--rule)}
  .letterhead .v-divider{top:44px;height:39px}
  .letterhead .v-divider.first{left:244px}
  .letterhead .v-divider.second{left:367px}
  .business-card .v-divider{left:295px;top:39px;height:91px}

  .address-block{position:absolute;left:272px;top:42px;font-size:9.6px;line-height:14.3px;color:var(--ink);font-style:normal}
  .contact-list{position:absolute;list-style:none}
  .contact-list li{display:flex;align-items:center;white-space:nowrap}
  .contact-list svg{flex:none;fill:none;stroke:var(--brand-blue);stroke-width:1.6;stroke-linecap:round;stroke-linejoin:round}
  .letterhead .contact-list{left:392px;top:42px;font-size:9.6px;line-height:14.3px;color:var(--ink)}
  .letterhead .contact-list li{gap:5px}
  .letterhead .contact-list svg{width:8px;height:8px}

  .header-rule{position:absolute;left:50px;top:90px;width:456px;height:1px;background:var(--rule)}

  .letter-body{position:absolute;left:50px;top:241px;width:456px}
  .salutation{font-family:"Mulish",Arial,sans-serif;font-weight:700;font-size:12px;color:var(--ink);margin-left:1px;margin-bottom:17px}
  .letter-body p.copy{font-size:9.4px;line-height:11.45px;color:var(--ink-soft);margin-bottom:10px}
  .closing{font-family:"Mulish",Arial,sans-serif;font-weight:700;font-size:7px;color:var(--ink);position:absolute;left:51px;top:513px}
  .signature{position:absolute;left:51px;top:545px;width:91px;height:28px;background:linear-gradient(90deg,var(--sig-tone),#e4e5e9);border-radius:3px}

  .foot-band{position:absolute;left:0;bottom:0;width:100%}
  .letterhead .foot-band{height:10px}
  .business-card .foot-band{height:14px}

  .holder{position:absolute;left:318px;top:36px}
  .holder-name{font-weight:700;font-size:17.5px;color:var(--brand-blue);line-height:20px;white-space:nowrap}
  .holder-role{font-size:13px;color:var(--ink-soft);line-height:16px}
  .business-card .contact-list{left:318px;top:78px;font-size:12.6px;line-height:19.2px;color:var(--ink)}
  .business-card .contact-list li{gap:7px}
  .business-card .contact-list svg{width:11px;height:11px}
  .card-address{position:absolute;left:0;width:100%;top:156px;text-align:center;font-size:12.4px;color:var(--ink-soft)}
</style>
</head>
<body>

<section class="sheet letterhead" aria-label="Letterhead">
  <div class="brand"><span class="brand-square"></span>HARLOW BUILD</div>
  <span class="v-divider first"></span>
  <address class="address-block">Your Address<br>City<br>State, Zip 0000</address>
  <span class="v-divider second"></span>
  <ul class="contact-list">
    <li><svg viewBox="0 0 12 12"><path d="M3 1.5l1.6 2.2-1 1.1a6 6 0 0 0 2.6 2.6l1.1-1L9.5 8 8.6 9.8C5.5 9.6 2.4 6.5 2.2 3.4z"/></svg>555-014-2100</li>
    <li><svg viewBox="0 0 12 12"><rect x="1.5" y="2.8" width="9" height="6.4" rx=".8"/><path d="M1.8 3.3L6 6.4l4.2-3.1"/></svg>office@harlowbuild.com</li>
    <li><svg viewBox="0 0 12 12"><circle cx="6" cy="6" r="4.5"/><path d="M1.5 6h9M6 1.5c-2.4 2.6-2.4 6.4 0 9M6 1.5c2.4 2.6 2.4 6.4 0 9"/></svg>www.harlowbuild.com</li>
  </ul>
  <span class="header-rule"></span>

  <div class="letter-body">
    <p class="salutation">Dear Mr. Ellery,</p>
    <p class="copy">Lorem ipsum dolor sit amet, consectetuer adipiscing elit, sed diam nonmmy nibh euismod tincidunt ut laor eet dolore magna aliquam erat volutpat. Ut wisi enim ad minim veniam, quis nostrud exerci tationmcorper suscipit lobortis nisl ut aliquip ex ea commodo consequat. Duis autem vel eum iriure dolor in hendrerit in vulputate velit esse molestie consequat, vel illum dolore eu feugiat</p>
    <p class="copy">Rorem ipsum dolor sit amet, consectetuer adipiscing elit, sed diam nonmmy nibh euismod tincidunt ut laor eet dolore magna aliquam erat volutpat. Ut wisi enim ad minim veniam, quis nostrud exerci tationmcorper suscipit lobortis nisl ut aliquip ex ea commodo consequat. Duis autem vel eum iriure dolor in hendrerit in vulputate velit esse molest</p>
    <p class="copy">Dorem ipsum dolor sit amet, consectetuer adipiscing elit, sed diam nonmmy nibh euismod tincidunt ut laor eet dolore magna aliquam erat volutpat. Ut wisi enim ad minim veniam, quis nostrud exerci tationmcorper suscipit lobortis nisl ut aliquip ex ea commodo consequat. Duis autem vel eum iriure dolor in hendrerit in suscipit lobortis nisl ut aliquip ex ea commodo consequat. Duis autem vel eum iriure dolor in hendrerit in vulputate velit esse molestie consequat, vel illum</p>
    <p class="copy">Sorem ipsum dolor sit amet, consectetuer adipiscing elit, sed diam nonmmy nibh euismod tincidunt ut laor eet dolore magna aliquam erat volutpat. Ut wisi enim ad minim veniam, quis nostrud exerci tationmcorper suscipit lobortis nisl ut aliquip ex ea commodo consequat. Duis autem vel eum iriure dolor in</p>
  </div>
  <p class="closing">Sincerely,</p>
  <div class="signature" role="img" aria-label="Handwritten signature of the sender"></div>

  <svg class="foot-band" viewBox="0 0 555 10" preserveAspectRatio="none" aria-hidden="true">
    <polygon points="0,0 420,0 411,10 0,10" fill="var(--brand-blue)"/>
    <polygon points="428,0 555,0 555,10 419,10" fill="var(--brand-slate)"/>
  </svg>
</section>

<section class="sheet business-card" aria-label="Business card">
  <div class="brand"><span class="brand-square"></span>HARLOW BUILD</div>
  <span class="v-divider"></span>
  <div class="holder">
    <p class="holder-name">MARCUS ELLERY</p>
    <p class="holder-role">Manager</p>
  </div>
  <ul class="contact-list">
    <li><svg viewBox="0 0 12 12"><path d="M3 1.5l1.6 2.2-1 1.1a6 6 0 0 0 2.6 2.6l1.1-1L9.5 8 8.6 9.8C5.5 9.6 2.4 6.5 2.2 3.4z"/></svg>555-014-2100</li>
    <li><svg viewBox="0 0 12 12"><rect x="1.5" y="2.8" width="9" height="6.4" rx=".8"/><path d="M1.8 3.3L6 6.4l4.2-3.1"/></svg>office@harlowbuild.com</li>
    <li><svg viewBox="0 0 12 12"><circle cx="6" cy="6" r="4.5"/><path d="M1.5 6h9M6 1.5c-2.4 2.6-2.4 6.4 0 9M6 1.5c2.4 2.6 2.4 6.4 0 9"/></svg>www.harlowbuild.com</li>
  </ul>
  <p class="card-address">Your Address, City, State, Zip 0000</p>
  <svg class="foot-band" viewBox="0 0 547 14" preserveAspectRatio="none" aria-hidden="true">
    <polygon points="0,0 428,0 416,14 0,14" fill="var(--brand-blue)"/>
    <polygon points="438,0 547,0 547,14 426,14" fill="var(--brand-slate)"/>
  </svg>
</section>

</body>
</html>
```